I am starting a company that will help small businesses that are looking to raise money over the internet (i.e. crowd fund) in reliance of the JOBS Act and the new rules that have been recently passed.

Initially, the website will help a business figure out if it is qualified to raise money and if so, it will tell the business what information is required.

The various pages will need to gather information from the businesses through Yes/No questionnaires, drop-down lists and free text boxes -

I am still thinking about my company's name and don't have a logo - for now, please use the name "MLAH (marble lantern advisory hub)" - feel free to throw in an idea for a logo

Hi all - I was wondering if I could get some design suggestions that don't use stock photos- thanks

Based on the designs I have received so far, I don't think the description of my website is clear.  The website will NOT be a crowdfunding portal (i.e. it is not like plumvesta etc.)  It is an information website that will allow companies to determine if they are legally able to raise money online. 

If they are able to raise money online, then the company can sign-up for some paid services which include legal documents and agreements.

To help the design process, I've uploaded a draft of the questions that a company will need to answer to determine if it is able to raise money online.

The submitted designs should be for both the homepage as well as the pages on which the questions will be set out.

Thanks for taking the time to read.

small businesses that will be looking to raise money through crowd funding

Internet

• I need designs for the following pages:

1. Home page
- should be simple - links to 'about' page and 'blog' page
- room at the bottom for affiliate links/logos
- convey the message that there are many rules that need to be followed to legally crowd fund a company but that this website makes compliance easy
- prominent 'get started' button

2. Company questions pages
- laid out to ask ~ 5 questions:
- name of company (free text answer)
- amount raised in prior 12 months (drop down box)
- state of formation (drop down box)
- registered with the ODV (y/n)
- registered as an investment company (y/n)

- needs to be a help 'icon' beside the questions so that user can hover over the icon and get more information as to what the question is asking

3. Eligibility questions page
- list of ~25 questions (y/n) answers
-
4. Fund raising objectives page
- list of ~15 questions answers
- answers will be y/n, multiple choice, drop down menu or free text

5. Results page
- if company is not-eligible to proceed, display "Not Eligible" page with list of reasons why
- if company is eligible, display "Congratulations" page with link to "Sign-up and Continue"

6. Sign-up page
- name
- address
- e-mail etc.
- check box to agree to terms and conditions

7. 'blog' page

8. about / disclaimer page

```html
<!DOCTYPE html>
<html lang="en">
<head>
<meta charset="utf-8">
<title>Marble Lantern Advisory Hub</title>
<link href="https://fonts.googleapis.com/css2?family=Open+Sans:wght@400;600;700&display=swap" rel="stylesheet">
<style>
:root{
  --green:#4aa83a;--red:#b2362b;--red-btn:#d3503f;--blue:#1b5b98;
  --text:#555;--line:#e1e1e1;--hero:#f3f3f3;--footer:#2c2c2c;--footer-deep:#1e1e1e;
  --footer-head:#8cc63f;--dark-btn:#4a4a4a;
}
*{box-sizing:border-box;margin:0;padding:0}
html,body{width:1200px;height:2765px;overflow:hidden}
body{font-family:"Open Sans",Arial,sans-serif;color:var(--text);background:#fff;position:relative}
.abs{position:absolute}
/* header */
.site-header{left:0;top:0;width:1200px;height:129px}
.brand{left:100px;top:24px;display:flex;align-items:center;gap:14px}
.brand-mark{width:72px;height:72px;border-radius:50%;background:var(--green)}
.brand-name{font-size:29px;line-height:32px;color:#444;font-weight:400}
.account-links{right:110px;top:28px;font-size:13px;letter-spacing:.5px;font-weight:600}
.account-links span{margin-left:14px}
.account-links .signup{color:var(--blue)}.account-links .login{color:var(--red)}.account-links .help{color:#333}
.search{right:100px;top:60px;width:190px;height:30px;border:1px solid #ccc;border-radius:2px;font-size:12px;color:#999;padding:6px 10px;background:#fafafa}
.search svg{position:absolute;right:8px;top:7px}
.main-nav{left:0;top:129px;width:1200px;height:41px;background:linear-gradient(#5cbb47,#3f9d31);display:flex;justify-content:center;align-items:center;color:#fff;font-size:14px;font-weight:600}
.main-nav .sep{margin:0 14px;opacity:.85}
/* hero */
.hero{left:0;top:170px;width:1200px;height:431px;background:var(--hero)}
.hero-art{left:166px;top:20px;width:534px;height:395px;border-radius:6px;background:radial-gradient(circle at 55% 40%,#f6efc5,#e9e9e9 70%)}
.hero-copy{left:700px;top:82px;width:354px;text-align:right}
.hero-copy h1{font-size:32px;font-weight:600;color:var(--red);margin-bottom:14px;white-space:nowrap}
.hero-copy p{font-size:13px;line-height:21px;color:#555}
.btn{display:inline-block;color:#fff;font-weight:700;font-size:14px;border-radius:3px;padding:0 12px;height:38px;line-height:38px}
.hero-btns{right:146px;top:230px}
.btn-dark{background:var(--dark-btn)}.btn-red{background:var(--red-btn);margin-left:10px}
.hero-dots{left:1002px;top:395px;display:flex;gap:8px}
.hero-dots i{width:14px;height:14px;border-radius:50%;background:#aaa;display:block}
.hero-dots i:first-child{background:#777}
/* topic list */
.topics{left:101px;top:632px;width:300px;list-style:none}
.topics li{font-size:16px;color:var(--blue);height:41.5px;display:flex;align-items:center;gap:14px}
.topics li::before{content:"";width:12px;height:12px;background:var(--blue);clip-path:polygon(0 0,100% 0,100% 100%,0 100%,0 0,25% 20%,25% 80%,75% 50%,25% 20%)}
.col-rule{left:402px;top:640px;width:1px;height:402px;background:var(--line)}
/* features */
.features{left:435px;top:636px;width:665px;height:50px;display:flex}
.feature{flex:1;display:flex;align-items:center;gap:12px;font-size:15px;line-height:20px;color:#444;border-left:1px solid var(--line);padding-left:14px}
.feature:first-child{border:none;padding-left:0}
.features-rule{left:435px;top:709px;width:603px;height:1px;background:#ccc}
.welcome-title{left:435px;top:738px;font-size:25px;color:var(--red);font-weight:400}
.welcome-text{left:435px;top:795px;width:332px;font-size:13px;line-height:22px;color:#666;text-align:justify}
.welcome-text p+p{margin-top:14px}
.video{left:792px;top:798px;width:296px;height:186px;background:linear-gradient(135deg,#b89a25,#7b6a1c);border-radius:3px}
.video svg{position:absolute;left:112px;top:57px}
.get-started{left:858px;top:1000px;height:38px;background:#3d3d3d;border-radius:3px;color:#fff;font-size:15px;font-weight:700;padding:0 16px;line-height:38px;display:flex;align-items:center;gap:10px}
.get-started b{width:20px;height:20px;border-radius:50%;background:#777;display:inline-block;position:relative}
.get-started b::after{content:"";position:absolute;left:8px;top:5px;border:5px solid transparent;border-left:6px solid #fff}
.section-rule{left:101px;top:1082px;width:999px;height:1px;background:var(--line)}
/* steps */
.section-title{left:0;top:1102px;width:1200px;text-align:center;font-size:26px;font-weight:400;color:var(--red)}
.steps{left:110px;top:1167px;width:980px;display:grid;grid-template-columns:repeat(4,233px);column-gap:16px;row-gap:26px}
.step{height:403px;border:1px solid #ddd;border-radius:3px;padding:5px;box-shadow:0 1px 2px rgba(0,0,0,.06)}
.step-img{height:130px;border-radius:2px}
.step h3{font-size:14px;line-height:20px;height:40px;color:var(--blue);font-weight:600;margin:14px 5px 2px}
.step .label{font-size:13px;color:#444;margin:0 5px}
.step .desc{font-size:11.5px;line-height:19px;height:57px;color:#777;margin:12px 5px 0}
.bar{margin:14px 5px 0;height:9px;border-radius:5px;background:#e8e8e8;border:1px solid #d8d8d8;overflow:hidden}
.bar i{display:block;height:100%;background:var(--green)}
.step .count{display:flex;justify-content:space-between;margin:14px 5px 0;font-size:14px;font-weight:600;color:var(--red)}
.step .meta{display:flex;justify-content:space-between;margin:22px 5px 0;font-size:13px;color:#444}
/* featured */
.featured{left:101px;top:2049px;width:999px;height:269px;background:#ececec;border:1px solid #e0e0e0}
.featured-img{left:10px;top:12px;width:402px;height:245px;background:linear-gradient(135deg,#7b4a3a,#c48d6c 55%,#5b2f2b)}
.featured-body{left:436px;top:16px;width:540px}
.featured-body h3{font-size:16px;color:var(--blue);font-weight:600}
.featured-body .label{font-size:13px;color:#444;margin-top:10px}
.featured-body p{font-size:12px;line-height:21px;color:#555;margin-top:10px}
.featured-body .price{font-size:19px;color:var(--red);font-weight:600;margin-top:16px}
.featured-body .btn{margin-top:14px;background:#555}
/* partners */
.partners{left:101px;top:2362px;width:999px;height:50px;display:flex;justify-content:space-between;align-items:center}
.partner{display:flex;align-items:center;gap:8px;font-size:19px;font-weight:700;color:#8a8a8a}
.partner i{width:18px;height:18px;background:#b5b5b5;display:block}
.partner i.round{border-radius:50%}
/* footer */
.site-footer{left:0;top:2451px;width:1200px;height:251px;background:var(--footer);color:#ddd}
.fcol{top:32px;font-size:13px}
.fcol h4{font-size:16px;font-weight:400;color:var(--footer-head);margin-bottom:14px}
.fcol li{list-style:none;line-height:25px}
.newsletter p{font-size:12.5px;line-height:19px;color:#ccc;width:250px}
.field{width:245px;height:28px;background:#f2f2f2;border-radius:2px;color:#555;font-size:12px;padding:6px 14px;margin-top:10px}
.subscribe{margin:10px 0 0 152px;display:inline-block;background:linear-gradient(#6cc24e,#3f9d31);color:#fff;font-size:12px;font-weight:600;padding:5px 14px;border-radius:2px}
.social li{display:flex;align-items:center;gap:10px;line-height:33px}
.social li i{width:24px;height:24px;border-radius:50%;background:#f2f2f2;display:block}
.copyright{left:0;top:2702px;width:1200px;height:63px;background:var(--footer-deep);color:#aaa;font-size:13px;text-align:center;line-height:63px}
</style>
</head>
<body>

<header class="site-header abs">
  <div class="brand abs"><span class="brand-mark"></span><span class="brand-name">Marble Lantern<br>Advisory Hub</span></div>
  <div class="account-links abs"><span class="signup">SIGNUP</span> <span style="color:#999">/</span> <span class="login">LOGIN</span> <span style="color:#999">/</span> <span class="help">HELP</span></div>
  <div class="search abs">Search
    <svg width="16" height="16" viewBox="0 0 16 16"><circle cx="6.5" cy="6.5" r="4.5" fill="none" stroke="#222" stroke-width="2"/><line x1="10" y1="10" x2="14" y2="14" stroke="#222" stroke-width="2.5"/></svg>
  </div>
</header>

<nav class="main-nav abs">
  <span>HOME</span><span class="sep">/</span><span>ABOUT US</span><span class="sep">/</span><span>HOW IT WORKS</span><span class="sep">/</span><span>SERVICES</span><span class="sep">/</span><span>ELIGIBILITY CHECK</span><span class="sep">/</span><span>BLOG</span><span class="sep">/</span><span>CONTACT US</span>
</nav>

<section class="hero abs">
  <div class="hero-art abs" role="img" aria-label="Illustration of figures fitting puzzle pieces together around a light bulb"></div>
  <div class="hero-copy abs">
    <h1>Crowdfund by the rules</h1>
    <p>The JOBS Act sets many rules for raising money online.<br>Answer a few simple questions and we tell you if you<br>qualify and what information you will need.</p>
  </div>
  <div class="hero-btns abs"><span class="btn btn-dark">LEARN MORE</span><span class="btn btn-red">GET STARTED</span></div>
  <div class="hero-dots abs"><i></i><i></i><i></i><i></i></div>
</section>

<ul class="topics abs">
  <li>JOBS Act Overview</li><li>Who Can Raise Online</li><li>Offering Limits</li><li>State of Formation</li><li>ODV Registration</li><li>Investment Companies</li><li>Disclosure Documents</li><li>Investor Limits</li><li>Ongoing Reporting</li><li>More »</li>
</ul>
<div class="col-rule abs"></div>

<div class="features abs">
  <div class="feature"><svg width="40" height="38" viewBox="0 0 40 38"><path d="M20 2 L38 36 H2 Z" fill="#444"/><rect x="18" y="13" width="4" height="13" fill="#fff"/><rect x="18" y="29" width="4" height="4" fill="#fff"/></svg><span>Know the<br>rules</span></div>
  <div class="feature"><svg width="36" height="40" viewBox="0 0 36 40"><path d="M9 18 V12 a9 9 0 0 1 18 0 V18" fill="none" stroke="#444" stroke-width="4"/><rect x="3" y="17" width="30" height="22" rx="3" fill="#444"/></svg><span>Secure<br>answers</span></div>
  <div class="feature"><svg width="26" height="42" viewBox="0 0 26 42"><rect x="1" y="1" width="24" height="40" rx="3" fill="#444"/><rect x="4" y="6" width="18" height="27" fill="#fff"/><circle cx="13" cy="37" r="2" fill="#fff"/></svg><span>Works on<br>any device</span></div>
  <div class="feature"><svg width="42" height="40" viewBox="0 0 42 40"><circle cx="15" cy="15" r="14" fill="#444"/><circle cx="28" cy="26" r="13" fill="#444" stroke="#fff" stroke-width="2"/><text x="15" y="20" font-size="14" fill="#fff" text-anchor="middle" font-family="Arial">$</text><text x="28" y="31" font-size="14" fill="#fff" text-anchor="middle" font-family="Arial">€</text></svg><span>Legal docs<br>available</span></div>
</div>
<div class="features-rule abs"></div>

<h2 class="welcome-title abs">Welcome to Marble Lantern Advisory Hub</h2>
<div class="welcome-text abs">
  <p>We are not a crowdfunding portal. We help small businesses find out whether they may legally raise money online. Answer short yes/no questions, pick from simple lists and fill in a few text boxes, and we show you where you stand and what the rules require.</p>
  <p>If you qualify, sign up to receive the legal documents and agreements you need to raise money with confidence.</p>
</div>
<div class="video abs" role="img" aria-label="Video still introducing the eligibility check">
  <svg width="72" height="72" viewBox="0 0 72 72"><circle cx="36" cy="36" r="32" fill="rgba(0,0,0,.25)" stroke="#fff" stroke-width="5"/><path d="M28 22 L52 36 L28 50 Z" fill="#fff"/></svg>
</div>
<div class="get-started abs">GET STARTED <b></b></div>
<div class="section-rule abs"></div>

<h2 class="section-title abs">How The Check Works</h2>
<div class="steps abs">
  <article class="step"><div class="step-img" style="background:linear-gradient(#6a7fb8,#a3687a 60%,#5a3a3a)" role="img" aria-label="Photo of a town skyline"></div><h3>Company Questions:<br>tell us who you are</h3><p class="label">Step 1 of 8</p><p class="desc">Company name, money raised in the last 12 months, state of formation and registrations.</p><div class="bar"><i style="width:12%"></i></div><div class="count"><span>5 questions</span><span>12%</span></div><div class="meta"><span>About 3 min</span><span>Free</span></div></article>
  <article class="step"><div class="step-img" style="background:linear-gradient(90deg,#c9cdd2,#f2f4f5)" role="img" aria-label="Photo of a person working at a computer"></div><h3>Eligibility Questions:<br>can you raise online?</h3><p class="label">Step 2 of 8</p><p class="desc">A short list of yes/no questions that checks your business against the rules.</p><div class="bar"><i style="width:25%"></i></div><div class="count"><span>25 questions</span><span>25%</span></div><div class="meta"><span>About 8 min</span><span>Free</span></div></article>
  <article class="step"><div class="step-img" style="background:radial-gradient(circle at 45% 55%,#4aa0c8,#0e2a3a 60%,#e8eef2 100%)" role="img" aria-label="Photo of a hand holding a glass globe"></div><h3>Fund Raising Objectives:<br>your plans</h3><p class="label">Step 3 of 8</p><p class="desc">Yes/no, multiple choice, drop-down and free text answers about your raise.</p><div class="bar"><i style="width:38%"></i></div><div class="count"><span>15 questions</span><span>38%</span></div><div class="meta"><span>About 6 min</span><span>Free</span></div></article>
  <article class="step"><div class="step-img" style="background:linear-gradient(#9a9a9a,#5c5c5c)" role="img" aria-label="Photo of a row of parked cars"></div><h3>Your Results:<br>eligible or not</h3><p class="label">Step 4 of 8</p><p class="desc">See a clear result with the reasons behind it and what to do next.</p><div class="bar"><i style="width:50%"></i></div><div class="count"><span>1 summary</span><span>50%</span></div><div class="meta"><span>Instant</span><span>Free</span></div></article>
  <article class="step"><div class="step-img" style="background:linear-gradient(90deg,#3a3a3a,#8a8a8a 50%,#a0302a)" role="img" aria-label="Photo of office equipment and a phone"></div><h3>Sign-up and Continue:<br>create your account</h3><p class="label">Step 5 of 8</p><p class="desc">Name, address and e-mail, then agree to the terms and conditions.</p><div class="bar"><i style="width:62%"></i></div><div class="count"><span>6 fields</span><span>62%</span></div><div class="meta"><span>About 2 min</span><span>Free</span></div></article>
  <article class="step"><div class="step-img" style="background:linear-gradient(135deg,#d79a74,#4a90c0 60%,#2a5a7a)" role="img" aria-label="Photo of hands using a tablet"></div><h3>Legal Documents:<br>prepared for you</h3><p class="label">Step 6 of 8</p><p class="desc">Offering documents drafted from your answers and ready for review.</p><div class="bar"><i style="width:75%"></i></div><div class="count"><span>Paid service</span><span>75%</span></div><div class="meta"><span>2 to 3 days</span><span>From $549</span></div></article>
  <article class="step"><div class="step-img" style="background:linear-gradient(135deg,#e9ecef,#9fb6cc 60%,#4a6a8c)" role="img" aria-label="Photo of a tablet showing a chart on a desk"></div><h3>Agreements:<br>sign with investors</h3><p class="label">Step 7 of 8</p><p class="desc">Investor agreements and forms that follow the rules for online raises.</p><div class="bar"><i style="width:88%"></i></div><div class="count"><span>Paid service</span><span>88%</span></div><div class="meta"><span>1 to 2 days</span><span>From $299</span></div></article>
  <article class="step"><div class="step-img" style="background:radial-gradient(circle at 50% 45%,#6fa8d8,#2a5c9a 55%,#1a2f4a)" role="img" aria-label="Photo of a hand over a world globe"></div><h3>Ongoing Filings:<br>stay compliant</h3><p class="label">Step 8 of 8</p><p class="desc">Reminders and reports that keep your company in line after the raise.</p><div class="bar"><i style="width:100%"></i></div><div class="count"><span>Yearly</span><span>100%</span></div><div class="meta"><span>Ongoing</span><span>From $99</span></div></article>
</div>

<section class="featured abs">
  <div class="featured-img abs" role="img" aria-label="Photo of many hands stacked together"></div>
  <div class="featured-body abs">
    <h3>Eligible? Sign up and continue with confidence</h3>
    <p class="label">Compliance package</p>
    <p>Once your results show that you may raise money online, our paid services give you the legal documents and agreements the rules require. Every document is built from the answers you already gave, so there is nothing to repeat. Read the disclaimer on our about page before you begin.</p>
    <p class="price">Packages from: $549USD</p>
    <span class="btn">KNOW MORE</span>
  </div>
</section>

<div class="partners abs">
  <span class="partner"><i></i>Tallyleaf</span>
  <span class="partner"><i class="round"></i>Brightcart</span>
  <span class="partner">PennyGrove</span>
  <span class="partner">Ruddock</span>
  <span class="partner"><i class="round"></i>Emberline</span>
  <span class="partner"><i></i>Keepwell</span>
</div>

<footer class="site-footer abs">
  <div class="fcol abs" style="left:111px"><h4>Quick Links</h4><ul><li>Home</li><li>About us</li><li>How it works</li><li>Services</li><li>Blog</li><li>Get Started</li></ul></div>
  <div class="fcol abs" style="left:275px"><h4>Eligibility Check</h4><ul><li>Company Questions</li><li>Eligibility Questions</li><li>Fund Raising Objectives</li><li>Your Results</li><li>Sign-up</li></ul></div>
  <div class="fcol abs" style="left:494px"><h4>Support Links</h4><ul><li>Press</li><li>Disclaimer</li><li>Privacy Policy</li><li>Term of Use</li><li>Contact us</li></ul></div>
  <div class="fcol newsletter abs" style="left:655px"><h4>Newsletters Sign Up</h4><p>Sign up for our daily email by entering your information below</p><div class="field">Your name</div><div class="field">Email address</div><span class="subscribe">SUBSCRIBE</span></div>
  <div class="fcol social abs" style="left:958px"><h4>Connect With Us</h4><ul><li><i></i>Facenote</li><li><i></i>Chirpline</li><li><i></i>Linkring</li></ul></div>
</footer>
<div class="copyright abs">Copyright © 2013 &nbsp;Marble Lantern Advisory Hub. &nbsp;All rights reserved.</div>

</body>
</html>
```